Business Card Design Project

We are a construction company in Orange County, CA. We need a two sided business card. We would like the back to be our logo with web URL. Front should included Name, title, address, phone, fax and email address.

our address is
627 West Dorrance Blvd, Suite 308
Anaheim, CA 92718

Our logo files are attached.

Construction

```html
<!DOCTYPE html>
<html lang="en">
<head>
<meta charset="utf-8">
<title>Stonebay Business Card</title>
<link href="https://fonts.googleapis.com/css2?family=Source+Sans+3:wght@400;600;700&display=swap" rel="stylesheet">
<style>
  :root {
    --brand-blue: #1a4c80;
    --card-white: #ffffff;
    --backdrop: #e9e9e9;
  }
  * { margin: 0; padding: 0; box-sizing: border-box; }
  html, body {
    width: 1200px; height: 402px; overflow: hidden;
    background: var(--backdrop);
    font-family: "Source Sans 3", sans-serif;
  }
  .card {
    position: absolute; top: 60px;
    width: 511px; height: 291px;
    background: var(--brand-blue);
    overflow: hidden;
  }
  .card--front { left: 54px; }
  .card--back { left: 636px; }
  .front-swoosh { position: absolute; inset: 0; }
  .front-wordmark {
    position: absolute; left: 22px; top: 62px;
    font-weight: 700; font-size: 52px; line-height: 1;
    letter-spacing: -0.5px;
    color: var(--brand-blue);
  }
  .contact {
    position: absolute; right: 26px; top: 34px;
    text-align: right; color: var(--card-white);
    font-size: 13.5px; line-height: 17px;
  }
  .contact__name { font-weight: 700; font-size: 16.5px; line-height: 20px; }
  .contact__title { font-size: 14px; margin-bottom: 24px; }
  .contact__line { display: flex; justify-content: flex-end; align-items: center; gap: 5px; }
  .contact__line svg { width: 10px; height: 10px; fill: var(--card-white); }
  .contact__lines { margin-bottom: 28px; }
  .contact__line--gap { margin-top: 4px; }
  .contact__address { line-height: 18px; }
  .back-wordmark {
    position: absolute; inset: 0;
    display: flex; align-items: center; justify-content: center;
    font-weight: 700; font-size: 76px; letter-spacing: -1px;
    color: var(--card-white);
  }
</style>
</head>
<body>
  <section class="card card--front">
    <svg class="front-swoosh" viewBox="0 0 511 291" width="511" height="291" aria-hidden="true">
      <path fill="#ffffff" d="M0,0 H268 C360,70 340,205 0,276 Z"/>
      <path fill="#ffffff" d="M278,0 H300 C328,14 342,30 350,48 C330,26 306,10 278,0 Z"/>
      <path fill="#ffffff" d="M118,291 C220,282 300,255 332,220 C305,262 235,284 168,291 Z"/>
    </svg>
    <div class="front-wordmark">STONEBAY</div>
    <div class="contact">
      <div class="contact__name">Your Name</div>
      <div class="contact__title">Title</div>
      <div class="contact__lines">
        <div class="contact__line">
          <svg viewBox="0 0 10 10"><path d="M2,0.5 L3.6,2.6 L2.8,3.6 C3.4,5 4.9,6.5 6.4,7.2 L7.4,6.4 L9.5,8 L8.4,9.5 C4.5,9 1,5.5 0.5,1.6 Z"/></svg>
          <span>01-234-5678</span>
        </div>
        <div class="contact__line">
          <svg viewBox="0 0 10 10"><path d="M2.5,0.5 H7.5 V3 H2.5 Z M0.5,3.5 H9.5 V8 H8 V6.5 H2 V8 H0.5 Z M2.5,7 H7.5 V9.5 H2.5 Z"/></svg>
          <span>01-234-5678</span>
        </div>
        <div class="contact__line contact__line--gap">
          <svg viewBox="0 0 10 10"><path d="M0.5,2 H9.5 V8.5 H0.5 Z M1.2,2.6 L5,5.5 L8.8,2.6" stroke="#1a4c80" stroke-width="0.8"/></svg>
          <span>info@stonebay.com</span>
        </div>
        <div class="contact__line">
          <svg viewBox="0 0 10 10"><circle cx="5" cy="5" r="4.5"/><path d="M0.5,5 H9.5 M5,0.5 C3,3 3,7 5,9.5 M5,0.5 C7,3 7,7 5,9.5" stroke="#1a4c80" stroke-width="0.7" fill="none"/></svg>
          <span>www.stonebay.com</span>
        </div>
      </div>
      <div class="contact__address">
        627 West Dorrance Blvd<br>
        Suite 308, Anaheim<br>
        CA&nbsp; 92718
      </div>
    </div>
  </section>

  <section class="card card--back">
    <div class="back-wordmark">STONEBAY</div>
  </section>
</body>
</html>
```